TWR Business Cards that rock.

New company needs business cards. We are a sports company that writes apps for golf. Company business cards should reflect our fun outgoing attitude but they are not to be "cartoonie".

On the back, we would like to use the orchid app market icon and also be able to include a QR code so that our product is easy to find.

I have included a couple images and our company logo to be used as inspiration and incorporated as you see fit.

Target Market(s)

sports, golfers

Industry/Entity Type

Golf Course

Font styles to use
Serif
Sans Serif

Requirements
Must have
• Standard business info, no office phone, but mobile phone
• Company name is "Tall Willow Putt"
Nice to have
• Our tag line is:
• Connect
• You're In
• Let's Play!

```html
<!DOCTYPE html>
<html lang="en">
<head>
<meta charset="utf-8">
<title>Tall Willow Putt – Business Cards</title>
<link href="https://fonts.googleapis.com/css2?family=Montserrat:wght@400;500;600&display=swap" rel="stylesheet">
<style>
  :root {
    --bg: #2a2a2c;
    --blue-deep: #2e7fd0;
    --blue-bright: #1fb2ea;
    --blue-text: #1f6fc2;
    --green: #5bbf3a;
    --white: #ffffff;
    --ink: #2b2b2b;
    --sky-top: #4a6fb8;
    --sky-light: #cfe0f0;
    --grass: #4f8f2e;
    --grass-dark: #2f5a1c;
  }
  * { margin: 0; padding: 0; box-sizing: border-box; }
  html, body {
    width: 1200px; height: 852px; overflow: hidden;
    background: var(--bg);
    font-family: "Montserrat", Arial, sans-serif;
  }
  .sheet { position: relative; width: 1200px; height: 852px; }
  .card {
    position: absolute; width: 620px; height: 354px;
    border-radius: 22px; overflow: hidden;
    box-shadow: 0 10px 30px rgba(0,0,0,.45);
  }
  .card-front { left: 120px; top: 40px; }
  .card-back { left: 460px; top: 458px; }

  /* Front */
  .course-photo {
    position: absolute; inset: 0;
    background: linear-gradient(180deg, var(--sky-top) 0%, var(--sky-light) 38%, #8fb37a 52%, var(--grass) 70%, var(--grass-dark) 100%);
  }
  .front-title {
    position: absolute; left: 40px; top: 128px;
    color: var(--white); font-weight: 500; font-size: 46px;
    letter-spacing: 1px; text-transform: uppercase;
    text-shadow: 0 1px 4px rgba(0,0,0,.25);
  }

  /* Back */
  .back-art { position: absolute; inset: 0; }
  .back-title {
    position: absolute; left: 32px; top: 58px;
    color: var(--white); font-weight: 500; font-size: 42px;
    text-transform: uppercase; line-height: 1;
  }
  .back-tagline {
    position: absolute; left: 35px; top: 108px;
    color: var(--white); font-size: 19px; font-weight: 400;
  }
  .brand-mark {
    position: absolute; left: 130px; top: 236px;
    display: flex; align-items: center; gap: 12px;
  }
  .brand-square { width: 22px; height: 22px; background: var(--green); }
  .brand-name {
    color: var(--blue-text); font-weight: 600; font-size: 56px; letter-spacing: 1px;
  }
  .contact {
    position: absolute; left: 385px; top: 164px;
    color: var(--ink); font-size: 14px; line-height: 1.45; font-style: normal;
  }
  .contact-name {
    color: var(--blue-text); font-weight: 500; font-size: 21px;
    text-transform: uppercase; line-height: 1.2;
  }
  .contact-role { margin-bottom: 2px; }
  .contact-line { display: flex; align-items: center; gap: 8px; }
  .contact-line svg { width: 12px; height: 12px; flex: none; }
</style>
</head>
<body>
<main class="sheet">

  <section class="card card-front">
    <div class="course-photo" role="img" aria-label="Photo of a seaside golf course with trees, a winding cart path and sunlit sky"></div>
    <h1 class="front-title">Tall Willow Putt</h1>
  </section>

  <section class="card card-back">
    <svg class="back-art" viewBox="0 0 620 354" preserveAspectRatio="none" aria-hidden="true">
      <defs>
        <linearGradient id="backBlue" x1="0" y1="1" x2="1" y2="0">
          <stop offset="0" stop-color="var(--blue-bright)"/>
          <stop offset="1" stop-color="var(--blue-deep)"/>
        </linearGradient>
      </defs>
      <rect width="620" height="354" fill="url(#backBlue)"/>
      <path d="M0,354 L0,318 Q120,150 620,118 L620,354 Z" fill="var(--white)"/>
      <path d="M0,318 Q120,150 620,118" fill="none" stroke="var(--green)" stroke-width="6"/>
    </svg>

    <h2 class="back-title">Tall Willow Putt</h2>
    <p class="back-tagline">Connect · You're In · Let's Play!</p>

    <div class="brand-mark">
      <span class="brand-square"></span>
      <span class="brand-name">TWR</span>
    </div>

    <address class="contact">
      <div class="contact-name">Mara Keller</div>
      <div class="contact-role">Managing Partner</div>
      <div>Lindenweg 12, 40210</div>
      <div>Düsseldorf, Germany</div>
      <div class="contact-line">
        <svg viewBox="0 0 12 12"><path d="M2.5 1 L4.5 1 L5.3 3.5 L4 4.5 Q5 7 7.5 8 L8.5 6.7 L11 7.5 L11 9.5 Q11 11 9.5 11 Q1 10 1 2.5 Q1 1 2.5 1Z" fill="var(--blue-text)"/></svg>
        <span>+49 170 555 014 22</span>
      </div>
      <div class="contact-line">
        <svg viewBox="0 0 12 12"><rect x="1" y="2.5" width="10" height="7" fill="none" stroke="var(--blue-text)" stroke-width="1.3"/><path d="M1 2.5 L6 6.5 L11 2.5" fill="none" stroke="var(--blue-text)" stroke-width="1.3"/></svg>
        <span>info@tallwillowputt.com</span>
      </div>
      <div class="contact-line">
        <svg viewBox="0 0 12 12"><circle cx="6" cy="6" r="5" fill="none" stroke="var(--blue-text)" stroke-width="1.2"/><ellipse cx="6" cy="6" rx="2.2" ry="5" fill="none" stroke="var(--blue-text)" stroke-width="1"/><path d="M1 6 H11" stroke="var(--blue-text)" stroke-width="1"/></svg>
        <span>www.tallwillowputt.com</span>
      </div>
    </address>
  </section>

</main>
</body>
</html>
```